Thornvale Group needs a business card design

We need a new business card design using the logo recently selected in a logo competition on Pixel Bazaar. Our business is a consultancy specializing in aviation and energy and the winning business card design will promote an image of precision and professionalism with creativity.

Please use the logo with the name on the front of the card and use a complementary font. Make the back white with either the light grey or dark grey logo.

Target Market(s)

Senior finance and legal leaders at aviation and energy companies

Industry/Entity Type

Management Consulting

Contact Information for Business Card

Peter Castrell
President
Thornvale Group

www.thornvalegroup.example

(555) 204-6391
pc@thornvalegroup.example

Requirements
Must have
• Professional font that goes well with the logo font

```html
<!DOCTYPE html>
<html lang="en">
<head>
<meta charset="utf-8">
<title>Thornvale Group – Business Card</title>
<link rel="stylesheet" href="https://fonts.googleapis.com/css2?family=Open+Sans:wght@400;700&display=swap">
<style>
  :root {
    --page: #ecebe8;
    --card: #ffffff;
    --navy: #1d4f7e;
    --blue-top: #3a86b4;
    --blue-bottom: #16466f;
    --grey-light: #9a9b9d;
    --grey-dark: #5f6164;
    --white: #ffffff;
  }
  * { box-sizing: border-box; margin: 0; padding: 0; }
  html, body { width: 1200px; height: 913px; overflow: hidden; }
  body {
    background: var(--page);
    font-family: "Open Sans", Arial, sans-serif;
    position: relative;
  }
  .card {
    position: absolute;
    top: 313px;
    width: 510px;
    height: 287px;
    background: var(--card);
    box-shadow: 0 6px 18px rgba(0,0,0,.12);
    overflow: hidden;
  }
  .card--front { left: 60px; }
  .card--back { left: 630px; }
  .card__art { position: absolute; inset: 0; width: 100%; height: 100%; }

  .brand-name {
    position: absolute;
    display: flex;
    align-items: center;
    gap: 10px;
    font-weight: 400;
    color: var(--navy);
    white-space: nowrap;
    line-height: 1;
  }
  .brand-name__mark {
    display: block;
    width: .6em;
    height: .6em;
    background: var(--navy);
  }
  .card--front .brand-name {
    left: 26px; top: 128px;
    font-size: 22px;
  }
  .card--back .brand-name {
    left: 0; right: 0; top: 124px;
    justify-content: center;
    font-size: 36px;
    gap: 14px;
  }

  .contact {
    position: absolute;
    right: 24px; top: 100px;
    text-align: right;
    color: var(--white);
  }
  .contact__name { font-size: 19px; font-weight: 700; line-height: 1.2; }
  .contact__title { font-size: 11px; font-weight: 400; opacity: .9; margin-bottom: 14px; }
  .contact__line {
    display: flex; justify-content: flex-end; align-items: center; gap: 6px;
    font-size: 12.5px; line-height: 1.55;
  }
  .contact__icon { width: 10px; height: 10px; fill: none; stroke: var(--white); stroke-width: 1.4; }
</style>
</head>
<body>

<section class="card card--front" aria-label="Business card front">
  <svg class="card__art" viewBox="0 0 510 287" preserveAspectRatio="none" aria-hidden="true">
    <defs>
      <linearGradient id="panelBlue" x1="0" y1="0" x2="0" y2="1">
        <stop offset="0" stop-color="var(--blue-top)"/>
        <stop offset="1" stop-color="var(--blue-bottom)"/>
      </linearGradient>
      <linearGradient id="bandGrey" x1="0" y1="0" x2="1" y2="0">
        <stop offset="0" stop-color="var(--grey-light)"/>
        <stop offset="1" stop-color="var(--grey-dark)"/>
      </linearGradient>
    </defs>
    <polygon points="262,0 510,0 510,287 288,287" fill="url(#panelBlue)"/>
    <polygon points="262,0 330,0 288,287 228,287" fill="url(#bandGrey)"/>
  </svg>

  <div class="brand-name"><span class="brand-name__mark" aria-hidden="true"></span>Thornvale Group</div>

  <div class="contact">
    <div class="contact__name">Peter Castrell</div>
    <div class="contact__title">President</div>
    <div class="contact__line">(555) 204-6391
      <svg class="contact__icon" viewBox="0 0 10 10" aria-hidden="true"><path d="M2 1 L4 3 L3 4 Q4.5 6 6 7 L7 6 L9 8 L8 9 Q3 8.5 1 2 Z"/></svg>
    </div>
    <div class="contact__line">pc@thornvalegroup.example
      <svg class="contact__icon" viewBox="0 0 10 10" aria-hidden="true"><rect x="1" y="2" width="8" height="6"/><path d="M1 2 L5 5.5 L9 2"/></svg>
    </div>
    <div class="contact__line">www.thornvalegroup.example
      <svg class="contact__icon" viewBox="0 0 10 10" aria-hidden="true"><circle cx="5" cy="5" r="4"/><path d="M1 5 H9 M5 1 Q2.5 5 5 9 M5 1 Q7.5 5 5 9"/></svg>
    </div>
  </div>
</section>

<section class="card card--back" aria-label="Business card back">
  <div class="brand-name"><span class="brand-name__mark" aria-hidden="true"></span>Thornvale Group</div>
</section>

</body>
</html>
```